Eye Catching Email Marketing design

Our health care consulting firm is based in New York City. We sell health care consulting Services to medical practices (doctors). We need a powerful email marketing design to use as one of our primary selling tools to attract new clients. The Design should convey health care knowledge, expertise professionalism, cutting edge technology and the services we offer. <br/>The design should incorporate our logo and its colors (blue and white) but we want it to be eye catching and vibrant, so other colors be included. We are open to the designer's creativity. Any pictures used should show diversity (races)and should include women. Designers can find our logo and other graphics on our website at www harbor ridge advisory.com. Please feel free to ask questions.<br/><br/>

Target Market(s)

Health care professionals, executives and Doctors.

Colors

Designer to choose colors to be used in the design.

Requirements
Nice to have
• What ever the design feels will help make this design vibrant

```html
<!DOCTYPE html>
<html lang="en">
<head>
<meta charset="utf-8">
<title>Harbor Ridge Advisory – Newsletter</title>
<link rel="stylesheet" href="https://fonts.googleapis.com/css2?family=Roboto:wght@400;500;700&family=Nunito+Sans:wght@400;600&display=swap">
<style>
:root{
  --brand-navy:#0b3a8c;
  --brand-sky:#2a93cf;
  --ink:#1f1f1f;
  --body-ink:#3a3a3a;
  --white:#ffffff;
  --footer-bg:#1c1c1c;
  --muted:#d9d9d9;
}
*{margin:0;padding:0;box-sizing:border-box}
html,body{width:1200px;height:4906px;overflow:hidden;background:var(--white)}
body{position:relative;font-family:"Nunito Sans",sans-serif;color:var(--ink)}
.abs{position:absolute}
.heading{font-family:"Roboto",sans-serif;font-weight:700;color:var(--ink);text-transform:uppercase}
.brand-name{font-family:"Roboto",sans-serif;font-weight:500;color:var(--brand-navy);font-size:30px;display:flex;align-items:center;gap:14px}
.brand-dot{width:26px;height:26px;border-radius:50%;background:var(--brand-navy)}
.header-contact{font-family:"Roboto",sans-serif;font-size:30px;color:var(--ink);display:flex;align-items:center;gap:22px;letter-spacing:.5px}
.photo{display:block}
.hero-panel{left:716px;top:276px;width:450px;height:368px;background:var(--brand-sky);opacity:.95}
.hero-title{left:756px;top:302px;font-size:58px;line-height:69px;color:var(--white);letter-spacing:1px}
.btn{position:absolute;display:flex;align-items:center;justify-content:center;font-family:"Roboto",sans-serif;font-weight:700;color:var(--white);text-transform:uppercase;background:var(--brand-navy)}
.welcome-title{left:59px;top:874px;font-size:45px;line-height:59px}
.welcome-text{left:59px;top:1015px;width:580px;font-size:25px;line-height:42px;color:var(--body-ink)}
.section-title{left:0;width:1200px;text-align:center;font-size:45px}
.rule{height:5px;width:108px;left:546px;background:var(--brand-sky)}
.service{position:absolute;width:600px;height:682px;color:var(--white);text-align:center;padding:0 40px}
.service.sky{background:var(--brand-sky)}
.service.navy{background:var(--brand-navy)}
.service .icon{margin:80px auto 0;width:164px;height:164px;border-radius:50%;background:var(--white);display:flex;align-items:center;justify-content:center}
.service h3{font-family:"Roboto",sans-serif;font-weight:700;font-size:29px;margin-top:38px;letter-spacing:.5px}
.service p{font-size:26px;line-height:42px;margin-top:20px}
.news-title{font-family:"Roboto",sans-serif;font-weight:700;font-size:28px;letter-spacing:1px;color:var(--ink)}
.news-date{font-family:"Roboto",sans-serif;font-weight:500;font-size:24px;letter-spacing:1px;color:var(--brand-navy);display:flex;align-items:center;gap:12px}
.news-body{font-size:24px;line-height:39px;color:var(--body-ink)}
.footer{left:0;top:4166px;width:1200px;height:740px;background:var(--footer-bg)}
.quote-btn{left:337px;top:4098px;width:526px;height:91px;border-radius:46px;background:var(--brand-sky);font-size:36px;letter-spacing:2px}
.footer-contact{display:flex;align-items:center;gap:20px;color:var(--white)}
.circle-icon{width:56px;height:56px;border-radius:50%;background:var(--brand-sky);display:flex;align-items:center;justify-content:center}
</style>
</head>
<body>

<header>
  <div class="abs brand-name" style="left:40px;top:55px"><span class="brand-dot"></span>Harbor Ridge Advisory LLC</div>
  <div class="abs header-contact" style="left:676px;top:30px">
    <svg width="30" height="30" viewBox="0 0 24 24"><path fill="#0b3a8c" d="M6.6 10.8a15 15 0 0 0 6.6 6.6l2.2-2.2a1 1 0 0 1 1-.25 11.4 11.4 0 0 0 3.6.57 1 1 0 0 1 1 1V20a1 1 0 0 1-1 1A17 17 0 0 1 3 4a1 1 0 0 1 1-1h3.5a1 1 0 0 1 1 1c0 1.25.2 2.45.57 3.57a1 1 0 0 1-.25 1z"/></svg>
    (212) 555-0148</div>
  <div class="abs header-contact" style="left:676px;top:82px">
    <svg width="30" height="30" viewBox="0 0 24 24"><rect x="3" y="5" width="18" height="14" rx="1" fill="none" stroke="#0b3a8c" stroke-width="2"/><path d="M3 6l9 7 9-7" fill="none" stroke="#0b3a8c" stroke-width="2"/></svg>
    info@harborridgeadvisory.com</div>
</header>

<section class="hero">
  <svg class="abs photo" style="left:0;top:156px" width="1200" height="600" role="img" aria-label="Photo of a diverse team of doctors and administrators meeting around a table">
    <defs><linearGradient id="heroGrad" x1="0" y1="0" x2="1" y2="1"><stop offset="0" stop-color="#5a4a3e"/><stop offset=".45" stop-color="#d9dadc"/><stop offset="1" stop-color="#a79a8c"/></linearGradient></defs>
    <rect width="1200" height="600" fill="url(#heroGrad)"/>
  </svg>
  <div class="abs hero-panel"></div>
  <h1 class="abs heading hero-title">Advancing<br>Healthcare<br>Operations</h1>
  <div class="btn" style="left:762px;top:537px;width:217px;height:69px;font-size:26px">Read More</div>
</section>

<section class="welcome">
  <h2 class="abs heading welcome-title">Welcome to Harbor Ridge<br>Advisory</h2>
  <p class="abs welcome-text">Harbor Ridge Advisory (HRA), founded in 2015, is a Management Services Organization &amp; Healthcare Consulting Firm skilled at helping medical practices advance their strategic vision in an ever-evolving healthcare system. Harbor Ridge Advisory specializes in Revenue Cycle</p>
  <div class="btn" style="left:59px;top:1295px;width:219px;height:69px;font-size:26px">Read More</div>
  <svg class="abs photo" style="left:665px;top:857px" width="484" height="526" role="img" aria-label="Photo of a smiling female doctor in a white coat with colleagues behind her">
    <defs><linearGradient id="welcomeGrad" x1="0" y1="0" x2="0" y2="1"><stop offset="0" stop-color="#c9dbe6"/><stop offset=".6" stop-color="#f1f2f4"/><stop offset="1" stop-color="#7e8a96"/></linearGradient></defs>
    <rect width="484" height="526" fill="url(#welcomeGrad)"/>
  </svg>
</section>

<section class="services">
  <h2 class="abs heading section-title" style="top:1498px">How can we help you?</h2>
  <div class="abs rule" style="top:1579px"></div>

  <div class="service sky" style="left:0;top:1640px">
    <div class="icon"><svg width="96" height="96" viewBox="0 0 48 48"><g fill="none" stroke="#2a93cf" stroke-width="5"><path d="M10 24a14 14 0 0 1 24-10"/><path d="M38 24a14 14 0 0 1-24 10"/></g><path d="M30 8l8 2-2 8z M18 40l-8-2 2-8z" fill="#2a93cf"/></svg></div>
    <h3>REVENUE CYCLE MANAGEMENT</h3>
    <p>Harbor Ridge Advisory understands the reimbursement landscape and is skilled in helping medical practices improve their margins. We can help you with medical billing &amp; coding, credentialing, A/R management &amp; staff training.</p>
  </div>
  <div class="service navy" style="left:600px;top:1640px">
    <div class="icon"><svg width="90" height="90" viewBox="0 0 48 48"><path d="M12 6h22v30a6 6 0 0 1-6 6H10a4 4 0 0 1-4-4h20V10" fill="none" stroke="#0b3a8c" stroke-width="4"/><path d="M24 14l8 3v6c0 5-4 8-8 9-4-1-8-4-8-9v-6z" fill="#2a93cf"/><path d="M20 23l3 3 5-6" fill="none" stroke="#fff" stroke-width="2.5"/></svg></div>
    <h3>COMPLIANCE MANAGEMENT</h3>
    <p>In a heavily regulated healthcare environment, medical practices need to be acutely aware of regulations or face huge fines. HRA can help you with risk assessments, compliance plans, clinical documentation audits, safety procedures</p>
  </div>
  <div class="service navy" style="left:0;top:2322px">
    <div class="icon"><svg width="96" height="96" viewBox="0 0 48 48"><circle cx="24" cy="24" r="16" fill="none" stroke="#0b3a8c" stroke-width="6" stroke-dasharray="5 3"/><circle cx="24" cy="18" r="5" fill="#2a93cf"/><path d="M15 34c0-6 4-9 9-9s9 3 9 9z" fill="#2a93cf"/></svg></div>
    <h3>HEALTHCARE INNOVATION</h3>
    <p>Do you want to enhance clinical operations and workflows? Are you looking to expand patient access and improve margins? HRA can help you integrate new technology into your practice including, telemedicine, service desk solutions, AI</p>
  </div>
  <div class="service sky" style="left:600px;top:2322px">
    <div class="icon"><svg width="96" height="96" viewBox="0 0 48 48"><circle cx="24" cy="15" r="6" fill="none" stroke="#0b3a8c" stroke-width="4" stroke-dasharray="3 2"/><path d="M6 22l6 14h8v-6l-6-4zM42 22l-6 14h-8v-6l6-4z" fill="#2a93cf"/></svg></div>
    <h3>PRACTICE MANAGEMENT</h3>
    <p>Practice Management requires the right balance of skill, knowledge, management &amp; business expertise. HRA can help strategically grow your practice by expanding patient access, optimizing scheduling, enhancing the patient experience</p>
  </div>
</section>

<section class="news">
  <h2 class="abs heading section-title" style="top:3100px">In the News</h2>
  <div class="abs rule" style="top:3179px"></div>

  <svg class="abs photo" style="left:65px;top:3261px" width="480" height="341" role="img" aria-label="Photo of a stethoscope resting on a calculator keypad">
    <defs><linearGradient id="newsGradA" x1="0" y1="0" x2="1" y2="1"><stop offset="0" stop-color="#c6d3de"/><stop offset=".5" stop-color="#3a4652"/><stop offset="1" stop-color="#eef2f5"/></linearGradient></defs>
    <rect width="480" height="341" fill="url(#newsGradA)"/>
  </svg>
  <div class="abs" style="left:608px;top:3297px;width:520px">
    <div class="news-title">REVENUE CYCLE CHALLENGES</div>
    <div class="news-date" style="margin-top:18px"><svg width="22" height="22" viewBox="0 0 24 24"><rect x="3" y="5" width="18" height="16" fill="none" stroke="#0b3a8c" stroke-width="2.5"/><path d="M8 13l3 3 5-6M7 2v5M17 2v5" fill="none" stroke="#0b3a8c" stroke-width="2.5"/></svg>JULY 05, 2020</div>
    <p class="news-body" style="margin-top:22px">Lorem ipsum dolor sit amet, consectetur adipiscing elit, sed do eiusmod tempor incididunt ut labore et dolore magna aliqua. Lorem ipsum dolor sit ametincididunt</p>
  </div>

  <div class="abs" style="left:67px;top:3687px;width:520px">
    <div class="news-title">COMMON PROBLEMS IN MEDICAL</div>
    <div class="news-date" style="margin-top:18px"><svg width="22" height="22" viewBox="0 0 24 24"><rect x="3" y="5" width="18" height="16" fill="none" stroke="#0b3a8c" stroke-width="2.5"/><path d="M8 13l3 3 5-6M7 2v5M17 2v5" fill="none" stroke="#0b3a8c" stroke-width="2.5"/></svg>JULY 05, 2020</div>
    <p class="news-body" style="margin-top:22px">Lorem ipsum dolor sit amet, consectetur adipiscing elit, sed do eiusmod tempor incididunt ut labore et dolore magna aliqua. Lorem ipsum dolor sit ametincididunt</p>
  </div>
  <svg class="abs photo" style="left:632px;top:3652px" width="479" height="341" role="img" aria-label="Photo of a hand writing beside a tall stack of paper files">
    <defs><linearGradient id="newsGradB" x1="0" y1="0" x2="1" y2="0"><stop offset="0" stop-color="#b89a86"/><stop offset=".55" stop-color="#6f7378"/><stop offset="1" stop-color="#e8e8ea"/></linearGradient></defs>
    <rect width="479" height="341" fill="url(#newsGradB)"/>
  </svg>
</section>

<footer>
  <div class="abs footer"></div>
  <div class="btn quote-btn">Get a Quote</div>
  <h2 class="abs heading section-title" style="top:4266px;color:var(--white)">Still have questions?</h2>
  <div class="abs rule" style="top:4347px"></div>
  <p class="abs" style="left:0;width:1200px;top:4382px;text-align:center;font-size:26px;color:var(--muted)">Talk to a Member of Our Team</p>
  <div class="abs footer-contact" style="left:170px;top:4458px;font-family:Roboto,sans-serif;font-size:34px;font-weight:500">
    <span class="circle-icon"><svg width="28" height="28" viewBox="0 0 24 24"><path fill="#fff" d="M6.6 10.8a15 15 0 0 0 6.6 6.6l2.2-2.2a1 1 0 0 1 1-.25 11.4 11.4 0 0 0 3.6.57 1 1 0 0 1 1 1V20a1 1 0 0 1-1 1A17 17 0 0 1 3 4a1 1 0 0 1 1-1h3.5a1 1 0 0 1 1 1c0 1.25.2 2.45.57 3.57a1 1 0 0 1-.25 1z"/></svg></span>
    (212) 555-0148</div>
  <div class="abs footer-contact" style="left:564px;top:4458px;font-size:28px">
    <span class="circle-icon"><svg width="28" height="28" viewBox="0 0 24 24"><rect x="3" y="5" width="18" height="14" rx="1" fill="none" stroke="#fff" stroke-width="2"/><path d="M3 6l9 7 9-7" fill="none" stroke="#fff" stroke-width="2"/></svg></span>
    info@harborridgeadvisory.com</div>
  <div class="abs brand-name" style="left:0;width:1200px;top:4640px;justify-content:center;font-size:34px;color:var(--brand-sky)">Harbor Ridge Advisory LLC</div>
  <p class="abs" style="left:0;width:1200px;top:4774px;text-align:center;font-size:26px;color:var(--muted)">© Copyright 2020 Harbor Ridge Advisory. All Rights Reserved.</p>
</footer>

</body>
</html>
```